Banner dimension 1767 X 887 for Tovrelli website

Need one banner for our website www.tovrelli.com.au, The dimension of the banner should be 1767 x 887. Attached to this brief are two images that needs to be on that one banner, PLEASE DO NOT SEND SEPARATE BANNERS, both images on the same banner. Thanks

The banner should have the following message on it:

1.) " Take a further 40% off all stock" ( use code: TOVRELLI. Ends 31/12/2015)
2.) " Kick back or kick it up a notch this Autumn in the most versatile pique striped polo shirts and Pinafore belt strap denim dress"

Target Market(s)

kids aged 5-12yrs

Requirements
Must have
• very playful

```html
<!DOCTYPE html>
<html lang="en">
<head>
<meta charset="utf-8">
<title>Tovrelli – Take a further 40% off all stock</title>
<link rel="stylesheet" href="https://fonts.googleapis.com/css2?family=Saira+Stencil+One&family=Oswald:wght@300;400&display=swap">
<style>
  :root {
    --teal: #1b7ea3;
    --magenta: #e4127f;
    --strip: #1c1c1e;
    --strip-text: #ffffff;
    --wash-lilac: #cfc3e3;
    --wash-blue: #bcd7e8;
    --wash-mint: #c9e6df;
    --paper: #f3f2f6;
  }
  * { margin: 0; padding: 0; box-sizing: border-box; }
  html, body { width: 1200px; height: 602px; overflow: hidden; background: #fff; }

  .banner {
    position: relative;
    width: 1200px;
    height: 602px;
    overflow: hidden;
    background: linear-gradient(120deg, var(--wash-blue) 0%, var(--wash-lilac) 30%, var(--paper) 50%, var(--wash-lilac) 70%, var(--wash-mint) 100%);
  }
  .watercolour-wash {
    position: absolute; inset: 0;
    background:
      radial-gradient(ellipse 320px 240px at 120px 120px, rgba(160,200,225,.55), transparent 70%),
      radial-gradient(ellipse 300px 260px at 1080px 460px, rgba(190,170,220,.55), transparent 70%),
      radial-gradient(ellipse 260px 200px at 980px 120px, rgba(180,220,215,.5), transparent 70%),
      radial-gradient(ellipse 280px 220px at 200px 500px, rgba(170,150,210,.45), transparent 70%);
  }
  .offer-panel {
    position: absolute; left: 335px; top: 0; width: 485px; height: 602px;
    background: rgba(255,255,255,.55);
  }

  .photo {
    position: absolute;
    border-radius: 40px 40px 8px 8px;
  }
  .photo--girl {
    left: 62px; top: 24px; width: 268px; height: 556px;
    background: linear-gradient(180deg, #6b4a3a 0%, #f1ece9 22%, #4f7394 45%, #6d8ca8 65%, #d9b8a6 82%, #e1607f 100%);
    opacity: .85;
  }
  .photo--boy {
    left: 778px; top: 58px; width: 342px; height: 512px;
    background: linear-gradient(180deg, #5b3b2a 0%, #d8a98c 18%, #3e8560 35%, #2a3a30 50%, #8fa9c2 68%, #c9a48f 82%, #2b2b2b 100%);
    opacity: .85;
  }

  .type { position: absolute; left: 0; top: 0; width: 1200px; height: 602px; }
  .type__sans { font-family: "Oswald", sans-serif; }
  .type__stencil { font-family: "Saira Stencil One", sans-serif; }
  .offer__lead { font-weight: 400; font-size: 60px; fill: var(--teal); }
  .offer__figure { font-size: 186px; fill: var(--magenta); }
  .offer__percent { font-size: 96px; fill: var(--magenta); }
  .offer__off { font-size: 74px; fill: var(--magenta); }
  .offer__scope { font-size: 72px; fill: var(--teal); }
  .offer__code { font-weight: 300; font-size: 44px; fill: var(--magenta); }
  .offer__code-word { font-weight: 400; }
  .offer__ends { font-weight: 300; font-size: 50px; fill: var(--teal); }

  .strip { fill: var(--strip); }
  .strip__text { font-weight: 400; fill: var(--strip-text); }
  .strip__text--headline { font-size: 27px; }
  .strip__text--line { font-size: 19px; }
</style>
</head>
<body>
<main class="banner">
  <div class="watercolour-wash" role="img" aria-label="Soft blue, lilac and mint watercolour texture background"></div>
  <div class="offer-panel"></div>

  <div class="photo photo--girl" role="img" aria-label="Smiling girl in a denim pinafore dress, white tee and pink sneakers"></div>
  <div class="photo photo--boy" role="img" aria-label="Playful boy in a green striped polo shirt and denim cargo shorts"></div>

  <svg class="type" viewBox="0 0 1200 602" xmlns="http://www.w3.org/2000/svg">
    <g class="offer">
      <text class="type__sans offer__lead" x="408" y="104" textLength="304" lengthAdjust="spacingAndGlyphs">TAKE A FURTHER</text>
      <text class="type__stencil offer__figure" x="408" y="248" textLength="198" lengthAdjust="spacingAndGlyphs">40</text>
      <text class="type__stencil offer__percent" x="614" y="186" textLength="98" lengthAdjust="spacingAndGlyphs">%</text>
      <text class="type__stencil offer__off" x="612" y="248" textLength="102" lengthAdjust="spacingAndGlyphs">OFF</text>
      <text class="type__stencil offer__scope" x="408" y="310" textLength="306" lengthAdjust="spacingAndGlyphs">ALL STOCK</text>
      <text class="type__sans offer__code" x="408" y="360" textLength="306" lengthAdjust="spacingAndGlyphs">use code: <tspan class="offer__code-word">TOVRELLI</tspan></text>
      <text class="type__sans offer__ends" x="408" y="406" textLength="304" lengthAdjust="spacingAndGlyphs">ends 31/12/2015</text>
    </g>

    <g class="strips">
      <rect class="strip" x="278" y="428" width="578" height="62"/>
      <rect class="strip" x="338" y="491" width="580" height="46"/>
      <rect class="strip" x="290" y="532" width="588" height="52"/>
      <text class="type__sans strip__text strip__text--headline" x="330" y="470" textLength="472" lengthAdjust="spacing">KICK BACK OR KICK IT UP A NOTCH</text>
      <text class="type__sans strip__text strip__text--line" x="377" y="522" textLength="505" lengthAdjust="spacing">THIS AUTUMN IN THE MOST VERSATILE PIQUE STRIPED</text>
      <text class="type__sans strip__text strip__text--line" x="325" y="566" textLength="517" lengthAdjust="spacing">POLO SHIRTS AND PINAFORE BELT STRAP DENIM DRESS</text>
    </g>
  </svg>
</main>
</body>
</html>
```